Packaging label design for Crystal water bottles

Hello, I am new to plotquarry and I am needing to have my packaging label designed for the crystal water bottles I'm manufacturing. The product name is Velumo Morrow Tide, the company is PELLVOT. The packaging is tube shaped cardboard like container, similar to what scotch bottles come in. I have included the diecut and the sample box that the manufacturer sent to me. Also included a photo of a concept idea and any logos or photos you may need.The font that is used for my logo is Pristina, if that can be used for everything but PELLVOT. (I used Proxima Nova for that)I would like the information on it to be: (and again this is just a concept I am open to adjustments and change) Morrow Tide- on the lid sectionAkasha by PELLVOT (I'm thinking that I might want this one a bit smaller and off set like a signature)500mlHighland, UT 84003www.akashacrystalenergy.comAnd have sacred geometry art on it such as Metatrons Cube, Fibonacci Spiral, or any other sacred geometry that might be appropriate or fitting.Again I am open to other options if you feel like you have a great idea for something different. Also i'm not sure if all the photos uploaded correctly, so let me know if one of them didn't work. Thank you.

```html
<!DOCTYPE html>
<html lang="en">
<head>
<meta charset="utf-8">
<title>Velumo Morrow Tide – Tube Label Dieline</title>
<link rel="stylesheet" href="https://fonts.googleapis.com/css2?family=Cinzel:wght@600&family=Italianno&family=Montserrat:wght@400&display=swap">
<style>
  :root {
    --paper: #ffffff;
    --frame: #222222;
    --dim: #29a8d8;
    --sand: #fcd889;
    --tan: #d2ad6b;
    --bronze: #a77f3b;
    --ink: #111111;
  }
  * { margin: 0; padding: 0; box-sizing: border-box; }
  html, body { width: 849px; height: 1200px; overflow: hidden; background: var(--paper); }
  .sheet {
    position: relative; width: 849px; height: 1200px;
    border: 1px solid var(--frame); background: var(--paper);
    font-family: "Montserrat", Arial, sans-serif;
  }
  .dim-label { position: absolute; color: var(--dim); font-family: Arial, sans-serif; font-size: 18px; line-height: 1; }
  .dim-label--vertical { transform: rotate(90deg); transform-origin: left top; white-space: nowrap; }
  .dim-lines { position: absolute; left: 0; top: 0; }

  .lid {
    position: absolute; top: 92px; width: 208px; height: 208px; border-radius: 50%;
    display: flex; flex-direction: column; align-items: center; justify-content: center; text-align: center;
  }
  .lid--maker { left: 104px; background: var(--sand); border: 2px solid var(--ink); }
  .lid--product { left: 443px; background: var(--tan); border: 1px solid #6b5530; }
  .lid__name {
    font-family: "Montserrat", Arial, sans-serif; font-size: 22px; line-height: 30px;
    letter-spacing: 3px; color: var(--ink);
  }

  .wrap { position: absolute; left: 78px; width: 686px; }
  .wrap__strip { background: var(--tan); height: 29px; border: 1px solid #8a6d3e; }
  .wrap__strip--top { top: 370px; }
  .wrap__strip--bottom { top: 1072px; }
  .wrap__band { top: 399px; height: 148px; background: var(--bronze); border-left: 1px solid #6b5530; border-right: 1px solid #6b5530; }
  .wrap__body { top: 547px; height: 525px; background: var(--sand); border: 1px solid #8a6d3e; }

  .geo-panel { position: absolute; }
  .geo-panel--band {
    left: 190px; top: 0; width: 310px; height: 148px;
    background: radial-gradient(ellipse at center 70%, rgba(210, 173, 107, 0.35), rgba(167, 127, 59, 0) 70%);
  }
  .geo-panel--left {
    left: 0; top: 20px; width: 200px; height: 490px;
    background: radial-gradient(ellipse at left center, rgba(205, 170, 110, 0.45), rgba(252, 216, 137, 0) 75%);
  }
  .geo-panel--right {
    right: 0; top: 20px; width: 220px; height: 490px;
    background: radial-gradient(ellipse at right center, rgba(205, 170, 110, 0.45), rgba(252, 216, 137, 0) 75%);
  }

  .band-title {
    position: absolute; left: 0; right: 0; top: 46px; text-align: center;
    font-family: "Cinzel", Georgia, serif; font-weight: 600; font-size: 52px; line-height: 1;
    letter-spacing: 4px; color: var(--sand);
  }

  .signature {
    position: absolute; left: 340px; top: 223px; transform: translate(-50%, -50%) rotate(-90deg);
    display: flex; flex-direction: column; align-items: flex-end; white-space: nowrap;
  }
  .signature__name { font-family: "Italianno", cursive; font-size: 130px; line-height: 0.75; color: var(--ink); }
  .signature__by { font-family: "Montserrat", Arial, sans-serif; font-size: 20px; line-height: 1; color: #333; margin-top: 2px; }

  .details {
    position: absolute; left: 0; right: 0; top: 445px; text-align: center;
    font-size: 16px; line-height: 21px; color: #222; letter-spacing: 0.6px;
  }
</style>
</head>
<body>
<div class="sheet">
  <span class="dim-label" style="left:325px; top:24px;">D:Φ83mm</span>

  <div class="lid lid--maker">
    <span class="lid__name">PELLVOT</span>
  </div>
  <div class="lid lid--product">
    <span class="lid__name">Velumo<br>Morrow Tide</span>
  </div>

  <span class="dim-label" style="left:4px; top:375px;">12mm</span>
  <span class="dim-label" style="left:4px; top:1077px;">12mm</span>

  <div class="wrap wrap__strip wrap__strip--top"></div>

  <div class="wrap wrap__band">
    <div class="geo-panel geo-panel--band" role="img" aria-label="Faint sacred geometry pattern behind the lid title"></div>
    <div class="band-title">MORROW TIDE</div>
  </div>

  <div class="wrap wrap__body">
    <div class="geo-panel geo-panel--left" role="img" aria-label="Sacred geometry line art, left side"></div>
    <div class="geo-panel geo-panel--right" role="img" aria-label="Sacred geometry line art, right side"></div>
    <div class="signature">
      <span class="signature__name">Velumo</span>
      <span class="signature__by">By PELLVOT</span>
    </div>
    <div class="details">
      <p>500ml</p>
      <p>Brindle Vale UT 84907</p>
      <p>www.velumomorrowtide.com</p>
    </div>
  </div>

  <div class="wrap wrap__strip wrap__strip--bottom"></div>

  <svg class="dim-lines" width="849" height="1200" aria-hidden="true">
    <g stroke="#29a8d8" stroke-width="1" fill="none">
      <line x1="764" y1="399" x2="795" y2="399"/>
      <line x1="764" y1="547" x2="795" y2="547"/>
      <line x1="772" y1="399" x2="772" y2="547"/>
      <line x1="764" y1="1072" x2="805" y2="1072"/>
      <line x1="772" y1="547" x2="772" y2="1072"/>
      <line x1="76" y1="1102" x2="76" y2="1137"/>
      <line x1="764" y1="1102" x2="764" y2="1137"/>
      <line x1="76" y1="1112" x2="764" y2="1112"/>
    </g>
  </svg>
  <span class="dim-label dim-label--vertical" style="left:806px; top:430px;">H:60mm</span>
  <span class="dim-label dim-label--vertical" style="left:806px; top:893px;">H:215mm</span>
  <span class="dim-label" style="left:377px; top:1124px;">W:280mm</span>
</div>
</body>
</html>
```